Banner Ad Design Project

Process description of accounting delivery A to Z

Your folder appointment for delivery of receipts, in and outgoing invoices not necessary but possible – goes into a industrial sized scanner at the office

Electronic delivery via email, Drivolen or remote scanning locally at the clients office

Imported into the accounting software (called Bilagio) with drag and drop from email and Drivolen our directly imported from scanner at clients office

Software sets ledger accounts after scanning largely automated
Imported into accounting softer and finished by producing Income statement , Balance sheet and cash flow statements.

Size should fit the www.brenvalo.no webpage banners rolling

Target Market(s)

New Clients - its to sell our work as modern

Industry/Entity Type

Accounting

Requirements
Must have
• Color scheme fitting current webpage. Looking for a process driven illustration where details are more 1D not 3D as such. Simplified and easy to grasp scheme of flow in our production pipeline.

```html
<!DOCTYPE html>
<html lang="en">
<head>
<meta charset="utf-8">
<title>Delivery Process Banners</title>
<link href="https://fonts.googleapis.com/css2?family=Mulish:wght@400;600;700&display=swap" rel="stylesheet">
<style>
  :root{
    --page:#ffffff;
    --panel:#ececec;
    --ink:#353535;
    --ink-soft:#4a4a4a;
    --green:#1f8a68;
    --rule:#a8a8a8;
    --badge:#7a7a7a;
  }
  *{margin:0;padding:0;box-sizing:border-box}
  html,body{width:1200px;height:1000px;overflow:hidden;background:var(--page)}
  body{position:relative;font-family:"Mulish",sans-serif;color:var(--ink)}
  .banner{position:absolute;left:216px;width:768px;height:240px;background:var(--panel)}
  .banner--en{top:207px}
  .banner--no{top:553px}
  .banner__title{position:absolute;top:20px;left:0;width:100%;text-align:center;font-size:16px;font-weight:700;color:var(--ink)}
  .banner__rules{position:absolute;left:0;top:0}
  .step{position:absolute}
  .step__num{position:absolute;left:0;top:0;width:19px;height:19px;border:2px solid var(--badge);border-radius:50%;font-size:11.5px;font-weight:700;color:var(--badge);display:flex;align-items:center;justify-content:center}
  .step__head{position:absolute;left:24px;top:0;white-space:nowrap;font-size:13.5px;font-weight:400;letter-spacing:-0.1px;color:var(--ink);line-height:17px}
  .step__sub{position:absolute;left:24px;top:16px;white-space:nowrap;font-size:9.5px;color:var(--ink-soft);line-height:12px}
  .or{position:absolute;left:31px;top:110px;font-size:13px;color:var(--ink)}
  .icon{position:absolute}
  .cloud-name{position:absolute;left:104px;top:185px;display:flex;align-items:center;gap:5px;font-size:17px;font-weight:400;color:var(--ink-soft)}
  .cloud-name__dot{width:12px;height:12px;border-radius:50%;background:var(--ink-soft)}
  .software-name{position:absolute;left:361px;top:104px;display:flex;align-items:center;gap:6px;font-size:19px;font-weight:700;color:var(--green)}
  .software-name__mark{width:14px;height:14px;background:var(--green)}
  .phase{position:absolute;top:223px;font-size:10px;color:var(--ink-soft);transform:translateX(-50%);white-space:nowrap}
</style>
</head>
<body>

<!-- English banner -->
<section class="banner banner--en">
  <h2 class="banner__title">Standard &amp; Digital Delivery Process</h2>
  <svg class="banner__rules" width="768" height="240" viewBox="0 0 768 240">
    <g stroke="var(--rule)" stroke-width="1.3" stroke-dasharray="6 4" fill="none">
      <line x1="282" y1="72" x2="282" y2="216"/><line x1="525" y1="72" x2="525" y2="216"/>
      <line x1="32" y1="230" x2="125" y2="230"/><line x1="185" y1="230" x2="268" y2="230"/>
      <line x1="297" y1="230" x2="370" y2="230"/><line x1="436" y1="230" x2="510" y2="230"/>
      <line x1="540" y1="230" x2="610" y2="230"/><line x1="674" y1="230" x2="740" y2="230"/>
    </g>
    <g stroke="var(--rule)" stroke-width="1.8" fill="none" stroke-linecap="round" stroke-linejoin="round">
      <circle cx="282" cy="225" r="8"/><path d="M278 225H286M283 221.5L286.5 225L283 228.5"/>
      <circle cx="525" cy="225" r="8"/><path d="M521 225H529M526 221.5L529.5 225L526 228.5"/>
    </g>
  </svg>

  <div class="step" style="left:27px;top:68px"><span class="step__num">1</span><p class="step__head">Client delivers vouchers for scanning</p><p class="step__sub">and we prepare them for ledger entry</p></div>
  <span class="or">or</span>
  <svg class="icon" style="left:114px;top:103px" width="28" height="34" viewBox="0 0 28 34"><path d="M1 2l3 -1 3 1 3 -1 3 1 3 -1 3 1 3 -1 3 1 3-1v32l-3 -1 -3 1 -3 -1 -3 1 -3 -1 -3 1 -3 -1 -3 1 -3 -1z" fill="none" stroke="var(--green)" stroke-width="1.6"/><rect x="5" y="6" width="5" height="5" fill="var(--green)"/><g stroke="var(--green)" stroke-width="1.4"><line x1="5" y1="15" x2="14" y2="15"/><line x1="5" y1="18" x2="14" y2="18"/><line x1="5" y1="21" x2="14" y2="21"/><line x1="5" y1="24" x2="14" y2="24"/></g><text x="17" y="29" font-size="9" font-weight="700" fill="var(--ink)" font-family="Mulish,sans-serif">$</text></svg>
  <svg class="icon" style="left:156px;top:112px" width="12" height="12" viewBox="0 0 12 12"><path d="M6 1v10M1 6h10" stroke="var(--ink)" stroke-width="2.4"/></svg>
  <svg class="icon" style="left:176px;top:103px" width="37" height="34" viewBox="0 0 37 34"><path d="M22 1l13 12 -20 14 -13 -4z" fill="none" stroke="var(--ink)" stroke-width="2.6" stroke-linejoin="round"/><path d="M2 23l13 4 20-14v5l-20 14 -13-4z" fill="var(--ink)"/></svg>

  <div class="step" style="left:27px;top:146px"><span class="step__num">2</span><p class="step__head">Client delivers vouchers electronically</p><p class="step__sub">via email, Drivolen or remote scanning</p></div>
  <svg class="icon" style="left:54px;top:184px" width="35" height="24" viewBox="0 0 35 24"><rect x="1.5" y="1.5" width="32" height="21" rx="3" fill="none" stroke="var(--green)" stroke-width="3"/><path d="M5 6l12.5 9L30 6" fill="none" stroke="var(--green)" stroke-width="3"/></svg>
  <div class="cloud-name"><span class="cloud-name__dot"></span>Drivolen</div>
  <svg class="icon" style="left:208px;top:180px" width="48" height="30" viewBox="0 0 48 30"><rect x="1.5" y="1.5" width="31" height="21" fill="none" stroke="var(--green)" stroke-width="3"/><rect x="12" y="25" width="10" height="3" fill="var(--ink)"/><g fill="none" stroke="var(--ink)" stroke-width="2"><path d="M10 10a10 10 0 0 1 14 0"/><path d="M13 13a6 6 0 0 1 8 0"/></g><circle cx="17" cy="16" r="1.6" fill="var(--ink)"/><rect x="37" y="1" width="10" height="28" rx="1" fill="var(--green)"/><rect x="39" y="4" width="6" height="21" fill="var(--panel)"/></svg>

  <div class="step" style="left:290px;top:68px"><span class="step__num">3</span><p class="step__head">Import to accounting software</p><p class="step__sub">directly from scanner or by drag and drop</p></div>
  <div class="software-name"><span class="software-name__mark"></span>Bilagio</div>

  <div class="step" style="left:290px;top:146px"><span class="step__num">4</span><p class="step__head">The software creates ledger</p><p class="step__sub">for each account</p></div>
  <svg class="icon" style="left:361px;top:178px" width="120" height="36" viewBox="0 0 120 36"><g fill="var(--panel)" stroke="var(--ink)" stroke-width="1.6"><rect x="1" y="1" width="22" height="28"/><rect x="4" y="4" width="22" height="28"/><rect x="7" y="7" width="22" height="28"/></g><g stroke="var(--ink)" stroke-width="1.4"><line x1="11" y1="13" x2="25" y2="13"/><line x1="11" y1="17" x2="25" y2="17"/><line x1="11" y1="21" x2="25" y2="21"/><line x1="11" y1="25" x2="25" y2="25"/><line x1="11" y1="29" x2="25" y2="29"/></g><path d="M40 14l5 5 -5 5M46 14l5 5 -5 5" fill="none" stroke="var(--green)" stroke-width="3"/><path d="M65 1h20l6 6v28h-26z" fill="none" stroke="var(--green)" stroke-width="2.2"/><g stroke="var(--green)" stroke-width="1.6"><line x1="69" y1="9" x2="78" y2="9"/><line x1="69" y1="14" x2="84" y2="14"/><line x1="69" y1="19" x2="80" y2="19"/></g><circle cx="84" cy="28" r="4" fill="none" stroke="var(--green)" stroke-width="1.8"/></svg>

  <div class="step" style="left:534px;top:68px"><span class="step__num">5</span><p class="step__head">Generate reports</p><p class="step__sub">Income statement, balance sheet and<br>Cash flow statement</p></div>
  <svg class="icon" style="left:617px;top:116px" width="110" height="36" viewBox="0 0 110 36"><path d="M2 1h15l6 6v28h-21z" fill="none" stroke="var(--ink)" stroke-width="1.8"/><g stroke="var(--ink)" stroke-width="1.4"><line x1="6" y1="12" x2="13" y2="12"/><line x1="6" y1="16" x2="13" y2="16"/><line x1="6" y1="20" x2="13" y2="20"/><line x1="6" y1="24" x2="13" y2="24"/><line x1="6" y1="28" x2="13" y2="28"/></g><rect x="39" y="1" width="26" height="34" fill="none" stroke="var(--green)" stroke-width="1.8"/><rect x="43" y="5" width="6" height="6" fill="none" stroke="var(--green)" stroke-width="1.4"/><g stroke="var(--green)" stroke-width="1.4"><line x1="52" y1="7" x2="61" y2="7"/><line x1="43" y1="15" x2="61" y2="15"/><line x1="43" y1="19" x2="61" y2="19"/><line x1="43" y1="23" x2="61" y2="23"/><line x1="43" y1="27" x2="61" y2="27"/><line x1="43" y1="31" x2="61" y2="31"/></g><path d="M79 1h22l6 6v28h-28z" fill="none" stroke="var(--ink)" stroke-width="1.8"/><g stroke="var(--ink)" stroke-width="1.4"><line x1="83" y1="7" x2="92" y2="7"/><line x1="83" y1="11" x2="92" y2="11"/><line x1="83" y1="24" x2="103" y2="24"/><line x1="83" y1="28" x2="103" y2="28"/><line x1="83" y1="32" x2="103" y2="32"/></g><text x="96" y="19" font-size="10" font-weight="700" fill="var(--ink)" font-family="Mulish,sans-serif">$</text></svg>

  <span class="phase" style="left:155px">Delivery</span>
  <span class="phase" style="left:403px">Processing</span>
  <span class="phase" style="left:637px">Finalisation</span>
</section>

<!-- Norwegian banner -->
<section class="banner banner--no">
  <h2 class="banner__title">Standard &amp; Elektronisk - leveringsprosess</h2>
  <svg class="banner__rules" width="768" height="240" viewBox="0 0 768 240">
    <g stroke="var(--rule)" stroke-width="1.3" stroke-dasharray="6 4" fill="none">
      <line x1="282" y1="72" x2="282" y2="216"/><line x1="525" y1="72" x2="525" y2="216"/>
      <line x1="32" y1="230" x2="128" y2="230"/><line x1="182" y1="230" x2="268" y2="230"/>
      <line x1="297" y1="230" x2="376" y2="230"/><line x1="430" y1="230" x2="510" y2="230"/>
      <line x1="540" y1="230" x2="608" y2="230"/><line x1="672" y1="230" x2="740" y2="230"/>
    </g>
    <g stroke="var(--rule)" stroke-width="1.8" fill="none" stroke-linecap="round" stroke-linejoin="round">
      <circle cx="282" cy="225" r="8"/><path d="M278 225H286M283 221.5L286.5 225L283 228.5"/>
      <circle cx="525" cy="225" r="8"/><path d="M521 225H529M526 221.5L529.5 225L526 228.5"/>
    </g>
  </svg>

  <div class="step" style="left:27px;top:68px"><span class="step__num">1</span><p class="step__head">Kunden leverer bilag til skanning</p><p class="step__sub">og vi klargjør for føring</p></div>
  <span class="or">eller</span>
  <svg class="icon" style="left:114px;top:103px" width="28" height="34" viewBox="0 0 28 34"><path d="M1 2l3 -1 3 1 3 -1 3 1 3 -1 3 1 3 -1 3 1 3-1v32l-3 -1 -3 1 -3 -1 -3 1 -3 -1 -3 1 -3 -1 -3 1 -3 -1z" fill="none" stroke="var(--green)" stroke-width="1.6"/><rect x="5" y="6" width="5" height="5" fill="var(--green)"/><g stroke="var(--green)" stroke-width="1.4"><line x1="5" y1="15" x2="14" y2="15"/><line x1="5" y1="18" x2="14" y2="18"/><line x1="5" y1="21" x2="14" y2="21"/><line x1="5" y1="24" x2="14" y2="24"/></g><text x="17" y="29" font-size="9" font-weight="700" fill="var(--ink)" font-family="Mulish,sans-serif">$</text></svg>
  <svg class="icon" style="left:156px;top:112px" width="12" height="12" viewBox="0 0 12 12"><path d="M6 1v10M1 6h10" stroke="var(--ink)" stroke-width="2.4"/></svg>
  <svg class="icon" style="left:176px;top:103px" width="37" height="34" viewBox="0 0 37 34"><path d="M22 1l13 12 -20 14 -13 -4z" fill="none" stroke="var(--ink)" stroke-width="2.6" stroke-linejoin="round"/><path d="M2 23l13 4 20-14v5l-20 14 -13-4z" fill="var(--ink)"/></svg>

  <div class="step" style="left:27px;top:146px"><span class="step__num">2</span><p class="step__head">Kunden leverer elektronisk</p><p class="step__sub">via email, Drivolen eller fjernskanning</p></div>
  <svg class="icon" style="left:54px;top:184px" width="35" height="24" viewBox="0 0 35 24"><rect x="1.5" y="1.5" width="32" height="21" rx="3" fill="none" stroke="var(--green)" stroke-width="3"/><path d="M5 6l12.5 9L30 6" fill="none" stroke="var(--green)" stroke-width="3"/></svg>
  <div class="cloud-name"><span class="cloud-name__dot"></span>Drivolen</div>
  <svg class="icon" style="left:208px;top:180px" width="48" height="30" viewBox="0 0 48 30"><rect x="1.5" y="1.5" width="31" height="21" fill="none" stroke="var(--green)" stroke-width="3"/><rect x="12" y="25" width="10" height="3" fill="var(--ink)"/><g fill="none" stroke="var(--ink)" stroke-width="2"><path d="M10 10a10 10 0 0 1 14 0"/><path d="M13 13a6 6 0 0 1 8 0"/></g><circle cx="17" cy="16" r="1.6" fill="var(--ink)"/><rect x="37" y="1" width="10" height="28" rx="1" fill="var(--green)"/><rect x="39" y="4" width="6" height="21" fill="var(--panel)"/></svg>

  <div class="step" style="left:290px;top:68px"><span class="step__num">3</span><p class="step__head">Importeres til Bilagio</p><p class="step__sub">direkte fra skanner eller via dra og slipp</p></div>
  <div class="software-name"><span class="software-name__mark"></span>Bilagio</div>

  <div class="step" style="left:290px;top:146px"><span class="step__num">4</span><p class="step__head">Automatisert postering</p><p class="step__sub">for hver konto</p></div>
  <svg class="icon" style="left:361px;top:178px" width="120" height="36" viewBox="0 0 120 36"><g fill="var(--panel)" stroke="var(--ink)" stroke-width="1.6"><rect x="1" y="1" width="22" height="28"/><rect x="4" y="4" width="22" height="28"/><rect x="7" y="7" width="22" height="28"/></g><g stroke="var(--ink)" stroke-width="1.4"><line x1="11" y1="13" x2="25" y2="13"/><line x1="11" y1="17" x2="25" y2="17"/><line x1="11" y1="21" x2="25" y2="21"/><line x1="11" y1="25" x2="25" y2="25"/><line x1="11" y1="29" x2="25" y2="29"/></g><path d="M40 14l5 5 -5 5M46 14l5 5 -5 5" fill="none" stroke="var(--green)" stroke-width="3"/><path d="M65 1h20l6 6v28h-26z" fill="none" stroke="var(--green)" stroke-width="2.2"/><g stroke="var(--green)" stroke-width="1.6"><line x1="69" y1="9" x2="78" y2="9"/><line x1="69" y1="14" x2="84" y2="14"/><line x1="69" y1="19" x2="80" y2="19"/></g><circle cx="84" cy="28" r="4" fill="none" stroke="var(--green)" stroke-width="1.8"/></svg>

  <div class="step" style="left:534px;top:68px"><span class="step__num">5</span><p class="step__head">Generere rapporter</p><p class="step__sub">Resultat, Balanse og kontantstrøm</p></div>
  <svg class="icon" style="left:617px;top:116px" width="110" height="36" viewBox="0 0 110 36"><path d="M2 1h15l6 6v28h-21z" fill="none" stroke="var(--ink)" stroke-width="1.8"/><g stroke="var(--ink)" stroke-width="1.4"><line x1="6" y1="12" x2="13" y2="12"/><line x1="6" y1="16" x2="13" y2="16"/><line x1="6" y1="20" x2="13" y2="20"/><line x1="6" y1="24" x2="13" y2="24"/><line x1="6" y1="28" x2="13" y2="28"/></g><rect x="39" y="1" width="26" height="34" fill="none" stroke="var(--green)" stroke-width="1.8"/><rect x="43" y="5" width="6" height="6" fill="none" stroke="var(--green)" stroke-width="1.4"/><g stroke="var(--green)" stroke-width="1.4"><line x1="52" y1="7" x2="61" y2="7"/><line x1="43" y1="15" x2="61" y2="15"/><line x1="43" y1="19" x2="61" y2="19"/><line x1="43" y1="23" x2="61" y2="23"/><line x1="43" y1="27" x2="61" y2="27"/><line x1="43" y1="31" x2="61" y2="31"/></g><path d="M79 1h22l6 6v28h-28z" fill="none" stroke="var(--ink)" stroke-width="1.8"/><g stroke="var(--ink)" stroke-width="1.4"><line x1="83" y1="7" x2="92" y2="7"/><line x1="83" y1="11" x2="92" y2="11"/><line x1="83" y1="24" x2="103" y2="24"/><line x1="83" y1="28" x2="103" y2="28"/><line x1="83" y1="32" x2="103" y2="32"/></g><text x="96" y="19" font-size="10" font-weight="700" fill="var(--ink)" font-family="Mulish,sans-serif">$</text></svg>

  <span class="phase" style="left:155px">Levere</span>
  <span class="phase" style="left:403px">Behandle</span>
  <span class="phase" style="left:640px">Ferdigstille</span>
</section>

</body>
</html>
```